Design letter head and business card

Hello,

you should design a business card and letter paper for Kranichflug Marketing. In German we write this word with K insteat of C.

Company does not have a logo. But in general, we write Kranichflug Marketing in 2 lines.
First line red: KRANICHFLUG
Second line gray: MARKETING

Red (or wine red) and Gray / Black are our favorite colors.

Company slogan: "Fresh Ground Online Marketing".

Company offers SEO, SEM, SEA, AdWords, Conversion Optimization, Online Markting Consulting ...

The website is old, please do not use this as base for your task.

German letter paper sizes:
Viawable Dimensions : 210 x 297 mm
Needed file dimensions: 212 x 299 mm

Informations to include:

Address:
Kranichflug Marketing GmbH
Lindenweg 23
71592 Weinstadt
Germany

Geschäftsführer | CEO: Bernhard Olzner

Phone: +49 (0) 7151 846 27 05

Fax: +49 (0) 7151 846 27 88

Mail: info@kranichflug-beispiel.de

Web: www.kranichflug-beispiel.de

Amtsgericht Suttgart, HRB 537264

Bank: Rosenauer Bank
IBAN: DE827315480900XXXXXXXX
BIC: GENODES1RSQ

Thanks

Bernhard

Target Market(s)

People who likes to win the online marketing game.

Industry/Entity Type

Business

Contact Information for Business Card

Here is the personal text on the card:

Name:
Bernhard Olzner

Title:
Geschäftsführer | CEO

Address:
Kranichflug Marketing GmbH
Lindenweg 23
71592 Weinstadt
Germany

Phone:
+49 (0) 7151 846 27 05

Fax:
+49 (0) 7151 846 27 88

Mail:
olzner@kranichflug-beispiel.de

Web:
www.kranichflug-beispiel.de

Business Card:
Viewable Dimensions: 85 x 55 mm
Needed file dimensions: 87 x 57mm

Font styles to use
Sans Serif

Requirements
Nice to have
• It would be great to see the dynamics of a helicopter.

```html
<!DOCTYPE html>
<html lang="de">
<head>
<meta charset="utf-8">
<title>Kranichflug Marketing – Visitenkarte</title>
<link rel="stylesheet" href="https://fonts.googleapis.com/css2?family=Saira+Condensed:wght@300;700&family=Saira+Extra+Condensed:wght@300&display=swap">
<style>
  :root {
    --card-bg: #e6e6e8;
    --side-band: #a7a9ac;
    --ink-dark: #262626;
    --wine-red: #9b2023;
    --illustration-light: #c9c9cb;
    --illustration-mid: #b3b3b6;
  }
  html, body {
    margin: 0;
    padding: 0;
    width: 1200px;
    height: 2160px;
    overflow: hidden;
  }
  .card {
    position: relative;
    width: 1200px;
    height: 2160px;
    background: var(--card-bg);
    overflow: hidden;
  }
  .side-band {
    position: absolute;
    left: 0;
    top: 0;
    width: 138px;
    height: 100%;
    background: var(--side-band);
  }
  .hero-illustration {
    position: absolute;
    left: 305px;
    top: 580px;
    width: 590px;
    height: 470px;
  }
  .brand-block {
    position: absolute;
    left: 200px;
    width: 870px;
    text-align: center;
  }
  .wordmark {
    top: 1040px;
    font-family: "Saira Condensed", sans-serif;
    font-weight: 700;
    color: var(--ink-dark);
    line-height: 0.84;
    font-size: 152px;
    letter-spacing: 2px;
  }
  .wordmark span { display: block; }
  .slogan {
    top: 1335px;
    font-family: "Saira Extra Condensed", sans-serif;
    font-weight: 300;
    font-size: 88px;
    color: var(--ink-dark);
    letter-spacing: 1px;
    line-height: 1;
  }
  .website {
    top: 1955px;
    font-family: "Saira Condensed", sans-serif;
    font-weight: 700;
    font-size: 74px;
    color: var(--wine-red);
    line-height: 1;
  }
</style>
</head>
<body>
  <div class="card">
    <div class="side-band"></div>

    <svg class="hero-illustration" viewBox="0 0 590 470" role="img" aria-label="Illustration: gezeichneter Hubschrauber mit roten Rotorlinien und hängender Last">
      <defs>
        <radialGradient id="hero-tone" cx="50%" cy="45%" r="60%">
          <stop offset="0%" stop-color="var(--illustration-mid)"/>
          <stop offset="100%" stop-color="var(--card-bg)"/>
        </radialGradient>
      </defs>
      <rect width="590" height="470" fill="url(#hero-tone)"/>
    </svg>

    <div class="brand-block wordmark">
      <span>KRANICHFLUG</span>
      <span>MARKETING</span>
    </div>

    <div class="brand-block slogan">Fresh Ground Online Marketing</div>

    <div class="brand-block website">www.kranichflug-beispiel.de</div>
  </div>
</body>
</html>
```